Real Estate Media Company Business Card

’m looking for a modern, high-end, double-sided business card for:
Bright Harbor Studios LLC
(Real Estate Photography & Videography)
The design should feel clean, minimal, and premium, appealing to top real estate agents and brokers.
👉 Horizontal layout is preferred
👉 Vertical option is welcome but not required
⸻
Front Side (Main Information):
Include:
* Desmond Whitfield
* Bright Harbor Studios LLC
* Title (open to creative improvement)
* Phone Number
* Email
* Website
⸻
Services Section (VERY IMPORTANT):
This should be a key visual element, not an afterthought.
Services to Include:
* Cinematic Video
* Real Estate Photography
* Drone
* Social Media Reels
* Floor Plans
* Use clean, modern icons next to each service
* Icons should be simple, minimal, and consistent style (outline or thin line preferred)
* Option to place icons inside small circles (like reference)
Layout:
* Format services similar to a clean horizontal or grid-style list (like “example 2”)
* Keep spacing balanced and uncluttered
* Make this section visually appealing and easy to scan
⸻
Back Side:
* Keep it extremely minimal
* Only include the logo in a corner
* No additional text needed
⸻
Typography & Style:
* Modern, clean, slightly bold fonts (based on uploaded references)
* Strong hierarchy (name + services stand out most)
* Plenty of white/negative space
* Avoid clutter
⸻
Overall Feel:
* Luxury
* Modern
* Clean
* Confident
* High-end real estate branding
⸻
Notes for Designers:
* Simplicity is key
* Services section should feel polished and intentional
* This card should feel like something a top-producing real estate agent would keep
Target Market(s)
Real estate agent agents

```html
<!DOCTYPE html>
<html lang="en">
<head>
<meta charset="utf-8">
<title>Bright Harbor Studios – Business Card</title>
<link href="https://fonts.googleapis.com/css2?family=Ubuntu:wght@300;400;500&family=Comfortaa:wght@500&display=swap" rel="stylesheet">
<style>
  :root {
    --stage: #333333;
    --card: #ffffff;
    --panel: #fafbfa;
    --tile: #ececec;
    --ink: #1f1f1f;
    --ink-soft: #3a3a3a;
    --muted: #a9a9a9;
    --rule: #8a8a8a;
    --photo-light: #f4ece0;
    --photo-mid: #e3d3bd;
    --photo-wood: #c9a57f;
  }
  * { margin: 0; padding: 0; box-sizing: border-box; }
  html, body { width: 963px; height: 1200px; overflow: hidden; }
  body { background: var(--stage); position: relative; font-family: "Ubuntu", sans-serif; color: var(--ink); }

  .card { position: absolute; left: 89px; width: 785px; height: 448px; background: var(--card);
          box-shadow: 14px 16px 22px rgba(0,0,0,.45); overflow: hidden; }
  .card--photo { top: 108px; }
  .card--info { top: 643px; }

  .card__photo { position: absolute; inset: 0;
    background: linear-gradient(180deg, var(--photo-light) 0%, #efe4d4 45%, var(--photo-mid) 70%, var(--photo-wood) 100%); }

  .wordmark { position: absolute; text-align: center; font-family: "Comfortaa", sans-serif; font-weight: 500;
              color: var(--ink); text-transform: uppercase; line-height: 1.15; }
  .wordmark__dot { display: block; margin: 0 auto 8px; border: 1.5px solid var(--ink); border-radius: 50%; }
  .card--photo .wordmark { left: 612px; top: 40px; width: 170px; font-size: 15px; letter-spacing: 1px; }
  .card--photo .wordmark__dot { width: 40px; height: 40px; }

  .brand-panel { position: absolute; left: 53px; top: 0; width: 219px; height: 219px; background: var(--panel);
                 border-right: 1px solid #f0f0ee; }
  .brand-panel .wordmark { left: 0; width: 219px; top: 46px; font-size: 21px; letter-spacing: 1.5px; }
  .brand-panel .wordmark__dot { width: 62px; height: 62px; margin-bottom: 14px; }

  .contact { position: absolute; left: 394px; top: 36px; }
  .contact__name { font-size: 31px; font-weight: 400; letter-spacing: .2px; line-height: 1; }
  .contact__name span { color: var(--muted); }
  .contact__title { margin-top: 4px; font-size: 15px; font-weight: 300; letter-spacing: 6px; color: var(--ink-soft); }
  .contact__rule { width: 37px; height: 1px; background: #c9c9c9; margin: 8px 0 12px; }
  .contact__list { list-style: none; font-size: 17.5px; font-weight: 300; color: var(--ink-soft); }
  .contact__list li { display: flex; align-items: center; height: 25px; }
  .contact__list svg { width: 12px; height: 12px; margin-right: 9px; flex: none; }

  .services__title { position: absolute; left: 39px; width: 708px; top: 220px; display: flex; align-items: center;
                     gap: 10px; font-size: 21px; font-weight: 400; letter-spacing: 4.5px; color: var(--ink-soft); }
  .services__title::before, .services__title::after { content: ""; flex: 1; height: 1px; background: var(--rule); }

  .services { position: absolute; left: 39px; top: 259px; width: 708px; height: 149px; display: grid;
              grid-template-columns: repeat(5, 1fr); gap: 3px; list-style: none; }
  .service { background: var(--tile); text-align: center; padding-top: 14px; }
  .service__icon { display: block; width: 57px; height: 57px; margin: 0 auto; }
  .service__label { margin-top: 14px; font-size: 17px; font-weight: 400; line-height: 1.3; color: var(--ink-soft); }
</style>
</head>
<body>

  <section class="card card--photo">
    <div class="card__photo" role="img" aria-label="Bright, sunlit white kitchen with a long island, bar stools, lantern pendants and light wood floors"></div>
    <div class="wordmark">
      <span class="wordmark__dot"></span>Bright Harbor<br>Studios
    </div>
  </section>

  <section class="card card--info">
    <div class="brand-panel">
      <div class="wordmark">
        <span class="wordmark__dot"></span>Bright Harbor<br>Studios
      </div>
    </div>

    <div class="contact">
      <h1 class="contact__name">Desmond <span>Whitfield</span></h1>
      <p class="contact__title">Owner</p>
      <div class="contact__rule"></div>
      <ul class="contact__list">
        <li><svg viewBox="0 0 12 12" fill="none" stroke="#888" stroke-width="1.2"><path d="M2 1.5l2 .2 1 2.5-1.2 1a6 6 0 0 0 3 3l1-1.2 2.5 1 .2 2c-5 .8-9.5-3.7-8.5-8.5z"/></svg>555 0148 2290</li>
        <li><svg viewBox="0 0 12 12" fill="none" stroke="#888" stroke-width="1.2"><rect x="1" y="2.5" width="10" height="7"/><path d="M1 2.5l5 4 5-4"/></svg>info@brightharborstudios.com</li>
        <li><svg viewBox="0 0 12 12" fill="none" stroke="#888" stroke-width="1.1"><circle cx="6" cy="6" r="5"/><path d="M1 6h10M6 1c-2.5 3-2.5 7 0 10M6 1c2.5 3 2.5 7 0 10"/></svg>www.brightharborstudios.com</li>
      </ul>
    </div>

    <h2 class="services__title">SERVICES</h2>
    <ul class="services">
      <li class="service">
        <svg class="service__icon" viewBox="0 0 57 57" fill="none" stroke="#333" stroke-width="1.2"><circle cx="28.5" cy="28.5" r="27.5"/><rect x="16" y="23" width="17" height="12" rx="2"/><path d="M33 27l7-4v12l-7-4"/></svg>
        <p class="service__label">Cinematic<br>Video</p>
      </li>
      <li class="service">
        <svg class="service__icon" viewBox="0 0 57 57" fill="none" stroke="#333" stroke-width="1.2"><circle cx="28.5" cy="28.5" r="27.5"/><path d="M17 23h6l2-3h7l2 3h6v14H17z"/><circle cx="28.5" cy="29.5" r="5"/><circle cx="28.5" cy="29.5" r="2.5"/></svg>
        <p class="service__label">Real Estate<br>Photography</p>
      </li>
      <li class="service">
        <svg class="service__icon" viewBox="0 0 57 57" fill="none" stroke="#333" stroke-width="1.2"><circle cx="28.5" cy="28.5" r="27.5"/><path d="M14 23h8M35 23h8M18 23v4M39 23v4M18 27h21"/><rect x="24" y="26" width="9" height="7" rx="2"/><circle cx="28.5" cy="31" r="1.5"/><path d="M24 33l-3 4M33 33l3 4"/></svg>
        <p class="service__label">Drone</p>
      </li>
      <li class="service">
        <svg class="service__icon" viewBox="0 0 57 57" fill="none" stroke="#333" stroke-width="1.2"><circle cx="28.5" cy="28.5" r="27.5"/><rect x="21" y="16" width="15" height="25" rx="2.5"/><path d="M26 19h5"/><path d="M26.5 25v8l6.5-4z"/><circle cx="28.5" cy="37.5" r=".8"/></svg>
        <p class="service__label">Social<br>Media Reels</p>
      </li>
      <li class="service">
        <svg class="service__icon" viewBox="0 0 57 57" fill="none" stroke="#333" stroke-width="1.2"><circle cx="28.5" cy="28.5" r="27.5"/><rect x="19" y="19" width="19" height="19"/><path d="M19 25l6-6M19 31l12-12M19 37l18-18M25 38l13-13M31 38l7-7"/></svg>
        <p class="service__label">Floor<br>Plans</p>
      </li>
    </ul>
  </section>

</body>
</html>
```